Business card for Crestline Bathrooms

Please design a business card for our bathroom renovation business. You can use my existing logo, but if you have an idea to modernize it, I would like to see it. Please see attached files first. I would like to use the blue and the orange theme. I like the concept of using the shower head in the logo. Please find following a design (or two) that I have been trying to create with my limited resources. That design was for a sign, but I was going to adopt it and use it as a business card as well. I like the concept of the water splash but I don’t think it “flows” nicely together with the logo. Another thought is that maybe creating the logo out of water splash could work and have a dramatic effect (like the water text and the butterfly picture attached with similar background instead of white). If the above doesn’t work I would like to see a modern simplified design. One of the attached files named as the unwanted business card has all the details that I want included in the business card. Please note that it is two sided.
Updates

I am very thankful for the designs that I have received, but they are very similar and only a couple of attempts to do something with the water splash as per my original brief. Modernizing the logo and having it made out of out of water splash with the orange as color accent could work and have a dramatic effect (like the water text and the butterfly picture attached with similar background instead of white). Please do not use the butterfly itself! This is just an example that images can be created out of water splash.

Contact Information for Business Card

all the details are on the unwonted business card file included

Colors
3176b5

Requirements
Nice to have
• Copied from the brief:
• ... maybe creating the logo out of water splash could work and have a dramatic effect (like the water text and the butterfly picture attached with similar background instead of white). Please do not use the butterfly itself!
Should not have
• I am getting designs with a butterfly. The butterfly picture was an example of creating something from a water splash. The butterfly itself has no association with anything other than the concept of creating a logo out of water splash. Sorry, I thought I was clear in the brief.

```html
<!DOCTYPE html>
<html lang="en">
<head>
<meta charset="utf-8">
<title>Crestline Bathrooms – Business Card</title>
<link href="https://fonts.googleapis.com/css2?family=Roboto:wght@400;500;700&family=Roboto+Condensed:wght@700&display=swap" rel="stylesheet">
<style>
  :root {
    --stage: #2a2a2a;
    --card-front: #e3f2fa;
    --card-back: #f1f1f1;
    --navy: #1b4d78;
    --brand-blue: #3176b5;
    --accent: #e8776a;
    --text-grey: #454545;
    --badge-grey: #5a5a5a;
    --water-light: #c6e7f6;
    --water-mid: #5fb8e2;
    --water-deep: #1283c2;
  }
  * { margin: 0; padding: 0; box-sizing: border-box; }
  html, body { width: 1200px; height: 960px; overflow: hidden; }
  body {
    background: var(--stage);
    font-family: "Roboto", Arial, sans-serif;
    position: relative;
  }
  .card {
    position: absolute;
    width: 598px;
    height: 342px;
    border-radius: 22px;
    overflow: hidden;
    box-shadow: 0 4px 10px rgba(0,0,0,0.45);
  }
  .card--front { left: 322px; top: 108px; background: linear-gradient(180deg, #eef8fd 0%, var(--card-front) 100%); }
  .card--back { left: 320px; top: 493px; background: var(--card-back); }

  .water-splash { position: absolute; left: 0; top: 0; width: 598px; height: 342px; }

  .contact { position: absolute; left: 0; right: 0; top: 40px; text-align: center; color: var(--text-grey); }
  .contact__name {
    font-family: "Roboto Condensed", "Roboto", sans-serif;
    font-weight: 700; font-size: 20px; color: var(--navy);
    letter-spacing: 0.5px; margin-bottom: 9px;
  }
  .contact__line { font-size: 14.5px; line-height: 19.5px; }
  .contact__web { letter-spacing: 1.6px; }

  .brand { position: absolute; left: 0; right: 0; top: 82px; display: flex; justify-content: center; align-items: center; gap: 12px; }
  .brand__dot { width: 18px; height: 18px; border-radius: 50%; background: var(--accent); }
  .brand__name { font-size: 32px; font-weight: 500; color: var(--navy); }

  .services { position: absolute; left: 0; right: 0; top: 187px; text-align: center; font-size: 14.5px; line-height: 18px; color: var(--text-grey); }

  .memberships { position: absolute; left: 0; right: 0; top: 275px; display: flex; justify-content: center; align-items: center; gap: 16px; }
  .memberships__badge--square { width: 32px; height: 34px; border-radius: 6px; background: var(--badge-grey); }
  .memberships__divider { width: 1px; height: 36px; background: var(--badge-grey); }
  .memberships__badge--wide { width: 116px; height: 26px; border-radius: 3px; background: var(--badge-grey); }
</style>
</head>
<body>

  <section class="card card--front">
    <svg class="water-splash" viewBox="0 0 598 342" role="img" aria-label="Blue water splash wave with droplets sweeping across the lower card">
      <defs>
        <linearGradient id="waterFill" x1="0" y1="0" x2="0" y2="1">
          <stop offset="0" stop-color="var(--water-light)"/>
          <stop offset="0.5" stop-color="var(--water-mid)"/>
          <stop offset="1" stop-color="var(--water-deep)"/>
        </linearGradient>
      </defs>
      <path d="M0 85 C60 95 110 180 200 185 C290 190 340 160 420 165 C500 170 550 150 598 155 L598 342 L0 342 Z" fill="url(#waterFill)"/>
    </svg>
    <div class="contact">
      <p class="contact__name">DANIEL MARSH</p>
      <p class="contact__line">PO Box 48, Riverton 2710 | P. 0400 555 218</p>
      <p class="contact__line">M. 5550 2194 E. daniel@crestlinebathrooms.com.au</p>
      <p class="contact__line contact__web">www.crestlinebathrooms.com.au</p>
    </div>
  </section>

  <section class="card card--back">
    <div class="brand">
      <span class="brand__dot"></span>
      <span class="brand__name">Crestline Bathrooms</span>
    </div>
    <div class="services">
      <p>Complete Bathroom Renovations &amp; Remodelling</p>
      <p>Highly Skilled &amp; Qualified Tradespeople</p>
      <p>Professional Service From Concept To Completion</p>
      <p>All Work Guaranteed</p>
    </div>
    <div class="memberships">
      <span class="memberships__badge--square"></span>
      <span class="memberships__divider"></span>
      <span class="memberships__badge--wide"></span>
    </div>
  </section>

</body>
</html>
```